A website where experts collaborate on your project

I am building a new website where experts (yes, like designers) collaborate on projects with the project owner. More minds = more collaboration = better end product. Please see Pelmora(dot)com for a quick landing page I created for collaborating on presentations (although there will be many project types offered)

I am looking for a DESIGNER LONG TERM, but for now, just need initial mock ups to show the web programmers.

I have 21 Word documents loosely designed, what I would like to see here is a theme. Please DO NOT GO OFF WHAT YOU CURRENTLY SEE AT PELMORA. What is up now is only a quick landing page.

You can view a Word doc of the homepage here:
https://www.filevanta.com/s/qx83kdm2/home.docx?dl=0

WHAT AM I LOOKING FOR?
A clean, well designed theme.

Here is a link to the logo:
https://www.filevanta.com/s/mr47tpz9/logo%20-%20horizontal.tif?dl=0
-----------------------------------------
Here are a few sites I like the design of and what I like about them:
www.quenbrook.com-all around my favorite, beautiful graphics, clean layout, bold use of colors on a dark background
Ravelto.com- clean layout, The use of humans and bubble style elements.
Mintharbor.com :) clean, bold, unique pop art style but professional
plumevault.com - From the unique colors and artwork and the ability of that art to not interfere with the important elements of the site
sparkwidgets.com-clean, nice colors, well organized and separated sections.
www.dunmereco.com-love the font, use of colors and sectionalized style

All in all, I am not picky and open to so many styles. I would ultimately like the designer I pick to design all 21 pages.
Updates

Hello everyone,Moving forward, I would like you all to pay special attention to the section in my brief titled "Here are a few sites I like the design of and what I like about them". Please see below, I handpicked each one of these as sites I really like. Thank you.Here are a few sites I like the design of and what I like about them:Ravelto.com- clean layout, The use of humans and bubble style elements.Mintharbor.com :) clean, bold, unique pop art style but professionalwriteraccess.com - From the unique colors and artwork and the ability of that art to not interfere with the important elements of the sitegrowthgeeks.com-clean, nice colors, well organized and separated sections.www.dunmereco.com-love the font, use of colors and sectionalized stylewww.quenbrook.com-beautiful graphics, clean layout, bold use of colors----------------------------------------- Added Tuesday, November 24, 2015

I updated the homepage, you can see it here:https://www.dropbox.com/s/kwlkbsookq3cg2m/1new%20homepage.docx?dl=0I am modeling it after my favorite designed site: triplelift.comI love the dark colors with the orange glowing style boldness of the buttons. It's real clean too. Added Tuesday, November 24, 2015

Target Market(s)

small business owners, marketers, freelancer writers, graphic designers,

Industry/Entity Type

Building

Number of Pages Required

5+ page

Requirements
Must have
• I can't think of anything the project must have.
Nice to have
• WHAT AM I LOOKING FOR?
• A clean, well designed theme. I had a designer do a bit of work putting elements together, I found it to be very plain, but I like the Application Page (https://www.filevanta.com/s/jb19ckr3/Pelmora-Website.ai?dl=0)
• Here is a link to the logo:
• https://www.filevanta.com/s/mr47tpz9/logo%20-%20horizontal.tif?dl=0
• Here are a few sites I like the design of and what I like about them:
• Ravelto.com- clean layout, The use of humans and bubble style elements.
• Mintharbor.com :) clean, bold, unique pop art style but professional
• plumevault.com - From the unique colors and artwork and the ability of that art to not interfere with the important elements of the site
• sparkwidgets.com-clean, nice colors, well organized and separated sections.
• www.dunmereco.com-love the font, use of colors and sectionalized style
• www.quenbrook.com-beautiful graphics, clean layout, bold use of colors
• -----------------------------------------
Should not have
• out of the boxed, templated style website. I want this site to be memorable and not look like a thousand others

```html
<!DOCTYPE html>
<html lang="en">
<head>
<meta charset="utf-8">
<title>Pelmora – Home</title>
<link href="https://fonts.googleapis.com/css2?family=Lato:wght@400;700&display=swap" rel="stylesheet">
<style>
:root{
  --orange:#f7901e;
  --teal:#58b3cc;
  --nav-teal:#4aa9c6;
  --ink:#333;
  --muted:#555;
  --panel:#f4f4f4;
  --dark:#1b1b1b;
  --darker:#111;
  --white:#fff;
}
*{box-sizing:border-box;margin:0;padding:0}
html,body{width:902px;height:1200px;overflow:hidden}
body{font-family:'Lato',sans-serif;color:var(--ink);background:var(--white);position:relative}
.abs{position:absolute}

.site-header{position:absolute;left:0;top:0;width:902px;height:76px;background:#fafafa;border-bottom:1px solid #e6e6e6}
.brand{left:80px;top:18px;display:flex;align-items:center;gap:8px}
.brand-name{font-size:22px;font-weight:700;color:var(--orange)}
.brand-mark{width:34px;height:34px;border-radius:50%;background:var(--orange)}
.search{left:305px;top:27px;width:166px;height:28px;border:1px solid #bcd;background:#fff;display:flex;align-items:center;padding-left:8px;gap:14px;font-size:9px;color:var(--nav-teal)}
.nav{left:497px;top:28px;display:flex;align-items:center;font-size:10px;color:#333}
.nav a{color:inherit;text-decoration:none;padding:0 12px;line-height:25px}
.nav a.active{background:var(--nav-teal);color:#fff;padding:0 10px;margin-right:2px}

.hero{left:0;top:76px;width:902px;height:283px;background:linear-gradient(90deg,#c9d2d8 0%,#dfe5ea 40%,#b9cbe3 60%,#9fb4cf 80%,#7e9a72 100%)}
.hero-title{left:0;top:117px;width:902px;text-align:center;font-size:25px;font-weight:700;color:#fff}
.hero-sub{left:0;top:151px;width:902px;text-align:center;font-size:15px;color:#fff}
.btn-orange{background:var(--orange);color:#fff;text-align:center}
.hero-btn{left:415px;top:184px;width:78px;height:30px;line-height:30px;font-size:9px}
.dots{left:434px;top:256px;display:flex;gap:5px}
.dots span{width:9px;height:9px;border-radius:50%;background:#fff}
.dots span:first-child{background:#333}

.sidebar-head{left:74px;top:379px;width:158px;height:29px;line-height:29px;padding-left:9px;font-size:10px}
.range-box{left:74px;top:408px;width:158px;height:66px;border:1px solid #ddd;border-top:none;background:#fff}
.range-label{left:8px;top:17px;font-size:8.5px;color:#333}
.filter-list{left:74px;top:474px;width:158px;height:194px;background:var(--panel);list-style:none;padding-top:7px}
.filter-list li{height:23.2px;font-size:9px;padding-left:25px;position:relative;line-height:17px}
.filter-list li::before{content:"";position:absolute;left:12px;top:5px;border-left:4px solid var(--nav-teal);border-top:3px solid transparent;border-bottom:3px solid transparent}
.save-btn{left:74px;top:683px;width:159px;height:35px;line-height:35px;font-size:15px}

.projects{left:263px;top:378px;width:550px;height:343px;background:var(--panel)}
.projects-head{left:0;top:0;width:550px;height:40px;background:var(--orange);color:#fff}
.projects-title{left:26px;top:12px;font-size:16px}
.sort{left:344px;top:14px;display:flex;gap:6px;font-size:8.5px;align-items:center}
.sort .on{background:var(--nav-teal);padding:2px 6px}
.sort span{margin-right:10px}
.project{left:31px;width:490px;font-size:8px;line-height:15.5px;color:#333}
.project .meta{color:var(--orange);margin-top:3px}
.rule{left:150px;width:252px;height:1px;background:#f1c9a0}
.view-btn{left:33px;top:291px;width:67px;height:25px;line-height:25px;background:var(--nav-teal);color:#fff;font-size:8.5px;text-align:center}

.testimonial{left:0;top:740px;width:902px;height:159px;background:var(--teal);color:#fff}
.avatar{left:97px;top:40px;width:94px;height:94px;border-radius:50%;border:3px solid #d8a24a;background:linear-gradient(#d6d9dc,#b4bac0)}
.t-title{left:210px;top:29px;font-size:16px;font-weight:700}
.t-body{left:213px;top:62px;width:605px;font-size:10.5px;line-height:15.5px}
.t-name{left:214px;top:115px;font-size:8.5px;font-weight:700}

.media{left:0;top:899px;width:902px;height:149px;background:#f7f7f7}
.media-title{left:0;top:26px;width:902px;text-align:center;font-size:16px;color:var(--teal)}
.media-row{left:78px;top:90px;width:745px;display:flex;justify-content:space-between;align-items:center;font-size:11px;font-weight:700;color:#555}
.media-row span{display:flex;align-items:center;gap:5px}
.media-row i{width:10px;height:10px;background:#9aa;display:inline-block}

.footer{left:0;top:1048px;width:902px;height:128px;background:var(--dark);color:#fff}
.f-title{left:0;top:20px;width:902px;text-align:center;font-size:19px;letter-spacing:.5px}
.f-body{left:0;top:57px;width:902px;text-align:center;font-size:9px;line-height:12px}
.social{left:385px;top:89px;display:flex;gap:5px}
.social span{width:18px;height:18px;border-radius:50%;background:var(--orange)}
.bottom-bar{left:0;top:1176px;width:902px;height:24px;background:var(--darker);color:#fff;font-size:8px}
.bottom-nav{left:82px;top:7px;display:flex;gap:28px}
.copy{left:679px;top:7px}
.ver{left:837px;top:7px}
</style>
</head>
<body>
<header class="site-header">
  <div class="abs brand"><span class="brand-name">Pelmora</span><span class="brand-mark"></span></div>
  <div class="abs search">
    <svg width="14" height="8" viewBox="0 0 14 8"><circle cx="3.5" cy="3.5" r="2.6" fill="none" stroke="#4aa9c6" stroke-width="1.3"/><line x1="5.5" y1="5.5" x2="7" y2="7" stroke="#4aa9c6" stroke-width="1.3"/><polyline points="10,3 11.5,4.5 13,3" fill="none" stroke="#4aa9c6"/></svg>
    FIND FREELANCERS
  </div>
  <nav class="abs nav"><a class="active">HOME</a><a>PROJECTS</a><a>HOW IT WORKS</a><a>PLAN</a><a>MY ACCOUNT</a></nav>
</header>

<section class="abs hero" role="img" aria-label="Photo of a smiling businessman in a blue shirt and tie in an office"></section>
<h1 class="abs hero-title">CONVET MORE COSTUMER</h1>
<p class="abs hero-sub">Experience the power of experts collaborating on your projects</p>
<div class="abs hero-btn btn-orange">Get Started</div>
<div class="abs dots"><span></span><span></span><span></span></div>

<aside>
  <div class="abs sidebar-head btn-orange" style="text-align:left">PRICE FILTER</div>
  <div class="abs range-box">
    <div class="abs range-label">Select your range</div>
    <svg class="abs" style="left:10px;top:38px" width="140" height="26" viewBox="0 0 140 26">
      <rect x="0" y="3" width="138" height="4" rx="2" fill="#333"/>
      <rect x="18" y="3" width="114" height="4" fill="#58b3cc"/>
      <path d="M14 2h8v4l-4 4-4-4z" fill="#58b3cc"/><path d="M128 2h8v4l-4 4-4-4z" fill="#58b3cc"/>
      <text x="7" y="23" font-size="8.5" fill="#4aa9c6" font-family="Lato,sans-serif">$ 20</text>
      <text x="105" y="23" font-size="8.5" fill="#4aa9c6" font-family="Lato,sans-serif">$ 1000+</text>
    </svg>
  </div>
  <ul class="abs filter-list">
    <li>PRICE</li><li>COUNTRY</li><li>CATEGORIES</li><li>TIME LEFT</li><li>ACTIVE / EXPIRED</li><li>CONTAIN ADULT CONTENT</li><li>KEYWORD</li><li>FOLLWERS</li>
  </ul>
  <div class="abs save-btn btn-orange">Save Filters</div>
</aside>

<main class="abs projects">
  <div class="abs projects-head">
    <div class="abs projects-title">CROWD PROJECTS</div>
    <div class="abs sort">Sort : <b class="on" style="font-weight:400">Prices</b><span></span>Contry<span></span>Time left</div>
  </div>
  <div class="abs project" style="top:61px">Ea vulputate mediocritatem ius, altera melius explicari an pro Ea vulputate mediocritatem ius, altera melius explicari an pro can we do in this in the window Ea vulputate mediocritatem ius, altera melius explicari an pro Ea vulputate mediocritatem ius, altera melius explicari an pro.<div class="meta">$350 , UK, Time left &nbsp;6 days</div></div>
  <div class="abs rule" style="top:131px"></div>
  <div class="abs project" style="top:139px">Ea vulputate mediocritatem ius, altera melius explicari an pro Ea vulputate mediocritatem ius, altera melius explicari an pro can we do in this in the window Ea vulputate mediocritatem ius, altera melius explicari an pro Ea vulputate mediocritatem ius, altera melius explicari an pro.<div class="meta">$350 , UK, Time left &nbsp;6 days</div></div>
  <div class="abs rule" style="top:209px"></div>
  <div class="abs project" style="top:217px">Ea vulputate mediocritatem ius, altera melius explicari an pro Ea vulputate mediocritatem ius, altera melius explicari an pro can we do in this in the window Ea vulputate mediocritatem ius, altera melius explicari an pro Ea vulputate mediocritatem ius, altera melius explicari an pro.<div class="meta">$350 , UK, Time left &nbsp;6 days</div></div>
  <div class="abs view-btn">View More</div>
</main>

<section class="abs testimonial">
  <div class="abs avatar" role="img" aria-label="Portrait photo of the client giving the testimonial"></div>
  <h2 class="abs t-title">TESTIMONIAL</h2>
  <p class="abs t-body">Lorem ipsum in the fringilla aenean pulvinar condimentum velit urna, suspendisse vivam us duis gravida psum lor lorem Erat fring-illa aenean pulvinar tum velit urna, suspendisse &nbsp;ipsum lor lorem. Lorem ipsum in the fringilla aenean pulvinar condimentum velit urna, suspendisse vivam us duis gravida</p>
  <div class="abs t-name">PETER</div>
</section>

<section class="abs media">
  <h2 class="abs media-title" style="font-weight:400">MEDIA LOGOS</h2>
  <div class="abs media-row">
    <span><i></i>Norvale</span><span>Kestrine</span><span>Brindle Labs</span><span>Solvane</span><span><i style="border-radius:50%"></i>Oakfield Trust</span><span>Harrowmere</span><span>Corvain Bank</span>
  </div>
</section>

<footer class="abs footer">
  <h2 class="abs f-title" style="font-weight:400">GET IN TOUCH</h2>
  <p class="abs f-body">Lorem ipsum dolor sit amet, consectetur adipiscing elit. Maurissemper eu turpis sed, mollis<br>vehicula neque. Ut in urna ante. Etiam sit amet arcu ante.</p>
  <div class="abs social"><span></span><span></span><span></span><span></span><span></span><span></span></div>
</footer>
<div class="abs bottom-bar">
  <div class="abs bottom-nav"><span>Home</span><span>Projecy</span><span>HoW it works</span><span>Plan</span><span>My Account</span><span>Contact Us</span></div>
  <div class="abs copy">Copyright© 2015. All Rights Reserved.</div>
  <div class="abs ver">M1</div>
</div>
</body>
</html>
```